Small corporate website template design

I need a couple templates designed for a small corporate website. The corporate site reflects the existence of the parent company which will own various brands/services that have their own websites, so it will mainly be used to present who we are, what we do, what is happening (news/events), how to contact us, link off to our other brand/service sites, as well as post information for public relations, investors, and job opportunities.

The company name is Brelvanto LLC (www.brelvanto-example.com), and the name is representative of stratified layers of interconnected digital services. The corporate site is not expected to generate a bunch of fanfare - that honor will be reserved for the externally linked brand/service sites.

The provided logo may be manipulated in color, size, shape, positioning, etc. to get it to fit with the design, but should be integrated in some way.

What we are looking for is a home page layout as well as a template for an inner page whereby the navigation/logo, etc may be diminished to some extent for the inner pages. We are also interested in reusable elements such as dividers, content containers, etc. in order to represent the types of information described above that we would like to present as described above.

We are particularly interested in consistency of design elements, conservative use of color (including consideration of accessibility concerns), judicious use of whitespace in favor of simplified messaging, and something lending itself well to internationalization/translation.

Target Market(s)

Small business owners, entrepreneurs (B2B)

Number of Pages Required

2 page

Font styles to use
Sans Serif

Requirements
Must have
• See the attached PDF with the logo concept, color swatches, and comparative sites.

```html
<!DOCTYPE html>
<html lang="en">
<head>
<meta charset="utf-8">
<title>Brelvanto LLC — Home</title>
<link rel="stylesheet" href="https://fonts.googleapis.com/css2?family=Roboto+Condensed:wght@400;500;700&family=Poppins:wght@400;500;600;700&family=Roboto:wght@400;500&family=Open+Sans:wght@400;700&display=swap">
<style>
:root{
  --navy-deep:#02081a;
  --navy:#061a4a;
  --blue:#0c3fa6;
  --blue-bright:#2f6fe0;
  --accent-blue:#4f7fc0;
  --icon-blue:#4a86dc;
  --orange:#f7881f;
  --ink:#1d1d1f;
  --text:#444;
  --white:#fff;
  --card-shadow:rgba(0,0,0,.18);
  --footer:#050a14;
}
*{margin:0;padding:0;box-sizing:border-box}
html,body{width:1200px;height:2885px;overflow:hidden}
body{position:relative;background:var(--white);font-family:'Poppins',sans-serif;color:var(--text)}
a{color:inherit;text-decoration:none}

/* Hero */
.hero{position:absolute;left:0;top:0;width:1200px;height:658px}
.hero-bg{position:absolute;inset:0;background:radial-gradient(ellipse at 50% 95%,#1565d8 0%,#0a3a9a 30%,#06204f 60%,#020a1e 100%)}
.site-header{position:absolute;left:0;top:0;width:1200px;height:150px}
.brand{position:absolute;left:132px;top:54px;font-family:'Roboto Condensed',sans-serif;font-weight:700;font-size:38px;color:var(--white);letter-spacing:.5px}
.main-nav{position:absolute;left:468px;top:64px;display:flex;align-items:center;font-family:'Roboto Condensed',sans-serif;font-size:17px;color:var(--white)}
.main-nav a{margin-right:25px}
.sign-in{border:2px solid var(--white);border-radius:18px;padding:4px 18px;font-weight:700;font-size:15px;letter-spacing:.5px;margin-left:5px}
.hero-title{position:absolute;left:0;width:1200px;top:258px;text-align:center;font-family:'Roboto Condensed',sans-serif;font-weight:500;font-size:43px;line-height:53px;color:var(--white)}
.btn-outline{display:inline-block;border:2px solid var(--white);border-radius:20px;color:var(--white);font-family:'Poppins',sans-serif;font-weight:500;text-align:center}
.hero-cta{position:absolute;left:505px;top:394px;width:190px;height:38px;line-height:34px;font-size:14px}
.hero-dots{position:absolute;left:563px;top:468px;display:flex;gap:9px;align-items:center}
.hero-dots span{width:11px;height:11px;border-radius:50%;background:var(--white)}
.hero-dots .active{width:18px;height:18px;border:2px solid var(--white);background:transparent;position:relative}
.hero-dots .active::after{content:"";position:absolute;left:3px;top:3px;width:8px;height:8px;border-radius:50%;background:var(--white)}

/* Services */
.section-title{position:absolute;left:0;width:1200px;top:744px;text-align:center;font-family:'Roboto',sans-serif;font-size:40px;color:var(--ink);font-weight:500}
.section-title .light{color:var(--accent-blue);font-weight:400}
.service-card{position:absolute;top:848px;width:298px;height:383px;background:var(--white);box-shadow:0 2px 10px var(--card-shadow);text-align:center}
.service-card svg{position:absolute;left:64px;top:38px}
.service-card h3{position:absolute;top:188px;width:100%;font-family:'Roboto',sans-serif;font-weight:500;font-size:18px;color:var(--ink)}
.service-card p{position:absolute;top:224px;left:14px;width:270px;font-size:12px;line-height:24px;color:var(--text)}
.btn-small{position:absolute;left:94px;top:313px;width:110px;height:32px;line-height:28px;border:2px solid #bbb;border-radius:16px;font-size:13px;color:var(--ink);box-shadow:0 1px 3px rgba(0,0,0,.15)}

/* What we do */
.what-band{position:absolute;left:0;top:1346px;width:1200px;height:520px}
.what-title{position:absolute;left:0;width:1200px;top:1484px;text-align:center;font-family:'Poppins',sans-serif;font-weight:600;font-size:40px;color:var(--white);letter-spacing:1px}
.what-text{position:absolute;left:170px;width:860px;top:1556px;text-align:center;font-size:13px;line-height:26px;color:var(--white)}
.what-cta{position:absolute;left:533px;top:1692px;width:134px;height:36px;line-height:32px;font-size:13.5px}

/* Investors */
.investor-art{position:absolute;left:125px;top:1932px;width:337px;height:356px;border-radius:6px;background:linear-gradient(160deg,#e8edf7 0%,#aebfe0 45%,#3b53b4 70%,#dfe5f2 100%)}
.investor-divider{position:absolute;left:504px;top:1996px;width:1px;height:244px;background:#ccc}
.investor-title{position:absolute;left:569px;top:1986px;font-family:'Roboto',sans-serif;font-weight:500;font-size:33px;color:var(--ink)}
.investor-text{position:absolute;left:569px;top:2050px;width:540px;font-size:12.5px;line-height:26px;color:var(--text)}
.btn-orange{position:absolute;left:569px;top:2212px;width:119px;height:33px;line-height:33px;text-align:center;border-radius:17px;background:var(--orange);color:var(--white);font-size:14px;box-shadow:0 2px 4px rgba(0,0,0,.2)}

/* Footer */
.footer-shape{position:absolute;left:0;top:2330px}
.footer-col{position:absolute;top:2498px;color:var(--white)}
.footer-col h4{font-family:'Poppins',sans-serif;font-weight:600;font-size:20px;margin-bottom:26px;letter-spacing:.3px}
.contact-list{list-style:none;font-size:12.5px;line-height:19px}
.contact-list li{position:relative;padding-left:32px;margin-bottom:18px}
.contact-list svg{position:absolute;left:0;top:1px}
.signup-text{font-size:11.5px;line-height:20px;width:290px}
.signup-form{display:flex;margin-top:22px;width:310px;height:32px}
.signup-input{flex:1;background:var(--white);border-radius:16px 0 0 16px;font-size:11px;color:#555;padding:9px 16px}
.signup-button{width:104px;background:var(--orange);border-radius:16px;margin-left:-16px;color:var(--white);font-weight:700;font-size:12px;line-height:32px;text-align:center}
.quick-links{list-style:none;font-size:12px;line-height:22px}
.footer-brand{position:absolute;left:934px;top:2560px;font-family:'Poppins',sans-serif;font-weight:600;font-size:28px;color:var(--white);letter-spacing:1px}
.footer-rule{position:absolute;left:0;top:2731px;width:1200px;height:1px;background:rgba(255,255,255,.15)}
.social{position:absolute;left:543px;top:2774px;display:flex;gap:6px}
.social span{width:25px;height:25px;border:1.5px solid var(--white);border-radius:50%}
.copyright{position:absolute;left:0;width:1200px;top:2824px;text-align:center;font-family:'Open Sans',sans-serif;font-size:13px;color:var(--white)}
</style>
</head>
<body>

<section class="hero">
  <div class="hero-bg" role="img" aria-label="Deep blue glowing network of connected nodes with faint security icons"></div>
  <header class="site-header">
    <div class="brand">BRELVANTO</div>
    <nav class="main-nav">
      <a href="#">HOME</a><a href="#">WHO WE ARE</a><a href="#">SERVICE</a><a href="#">INVESTORS</a><a href="#">NEWS</a><a href="#">CONTACT</a>
      <a href="#" class="sign-in">SIGN IN</a>
    </nav>
  </header>
  <h1 class="hero-title">ADAPTIVE SOFTWARE TECHNOLOGY<br>FOR THE DIGITAL REVOLUTION</h1>
  <a href="#" class="btn-outline hero-cta">JOB OPPORTUNITIES</a>
  <div class="hero-dots"><span class="active"></span><span></span><span></span><span></span></div>
</section>

<h2 class="section-title"><span class="light">OUR</span> SERVICES</h2>

<article class="service-card" style="left:129px">
  <svg width="170" height="110" viewBox="0 0 170 110">
    <circle cx="9" cy="28" r="6" fill="var(--icon-blue)"/><circle cx="157" cy="80" r="3.5" fill="var(--icon-blue)"/>
    <polygon points="85,2 132,29 132,81 85,108 38,81 38,29" fill="none" stroke="var(--icon-blue)" stroke-width="2"/>
    <polygon points="85,9 126,33 126,77 85,101 44,77 44,33" fill="var(--icon-blue)"/>
    <path d="M68 68 V44 M68 68 H104 M72 62 L82 52 L89 58 L101 46 M95 46 H101 V52" fill="none" stroke="#fff" stroke-width="3" stroke-linecap="round" stroke-linejoin="round"/>
  </svg>
  <h3>QUIS AUTEM VEL EUM</h3>
  <p>Sed ut perspiciatis unde omnis iste<br>natus error sit voluptatem accusantium<br>doloremque laudantium, totam</p>
  <a href="#" class="btn-small">Read More</a>
</article>

<article class="service-card" style="left:448px">
  <svg width="170" height="110" viewBox="0 0 170 110">
    <circle cx="9" cy="28" r="6" fill="var(--icon-blue)"/><circle cx="157" cy="80" r="3.5" fill="var(--icon-blue)"/>
    <polygon points="85,2 132,29 132,81 85,108 38,81 38,29" fill="none" stroke="var(--icon-blue)" stroke-width="2"/>
    <polygon points="85,9 126,33 126,77 85,101 44,77 44,33" fill="var(--icon-blue)"/>
    <path d="M77 52 V43 a10 10 0 0 1 20 0" fill="none" stroke="#fff" stroke-width="4"/>
    <rect x="70" y="52" width="30" height="24" rx="3" fill="#fff"/>
    <rect x="83" y="59" width="4" height="10" rx="2" fill="var(--icon-blue)"/>
  </svg>
  <h3>QUIS AUTEM VEL EUM</h3>
  <p>Sed ut perspiciatis unde omnis iste<br>natus error sit voluptatem accusantium<br>doloremque laudantium, totam</p>
  <a href="#" class="btn-small">Read More</a>
</article>

<article class="service-card" style="left:767px">
  <svg width="170" height="110" viewBox="0 0 170 110">
    <circle cx="9" cy="28" r="6" fill="var(--icon-blue)"/><circle cx="157" cy="80" r="3.5" fill="var(--icon-blue)"/>
    <polygon points="85,2 132,29 132,81 85,108 38,81 38,29" fill="none" stroke="var(--icon-blue)" stroke-width="2"/>
    <polygon points="85,9 126,33 126,77 85,101 44,77 44,33" fill="var(--icon-blue)"/>
    <path d="M85 34 a14 14 0 0 1 8 25 v5 h-16 v-5 a14 14 0 0 1 8 -25z" fill="#fff"/>
    <rect x="78" y="67" width="14" height="4" rx="2" fill="#fff"/><rect x="80" y="73" width="10" height="4" rx="2" fill="#fff"/>
  </svg>
  <h3>QUIS AUTEM VEL EUM</h3>
  <p>Sed ut perspiciatis unde omnis iste<br>natus error sit voluptatem accusantium<br>doloremque laudantium, totam</p>
  <a href="#" class="btn-small">Read More</a>
</article>

<svg class="what-band" width="1200" height="520" viewBox="0 0 1200 520" role="img" aria-label="Deep blue background of glowing connected network lines">
  <defs>
    <radialGradient id="bandGlow" cx="50%" cy="45%" r="70%">
      <stop offset="0" stop-color="#1a56c8"/><stop offset=".55" stop-color="#0a2a7a"/><stop offset="1" stop-color="#030c2c"/>
    </radialGradient>
  </defs>
  <polygon points="0,0 1200,42 1200,519 0,477" fill="url(#bandGlow)"/>
</svg>
<h2 class="what-title">WHAT WE DO</h2>
<p class="what-text">We are a team of U.S.-based systems developers &amp; administrators, technical consultants, and operational subject matter experts<br>that deliver highly customized, boutique, and/or enterprise level solutions to large government organizations and international<br>businesses. Our team has delivered highly technical cyber defense and communication solutions in over 50 countries in both<br>remote and austere environments as well as highly developed nations.</p>
<a href="#" class="btn-outline what-cta">READ MORE</a>

<div class="investor-art" role="img" aria-label="Isometric laptop showing charts and graphs"></div>
<div class="investor-divider"></div>
<h2 class="investor-title">BRELVANTO INVESTORS</h2>
<p class="investor-text">Sed ut perspiciatis unde omnis iste natus error sit voluptatem accusantium<br>doloremque laudantium, totam rem aperiam, eaque ipsa quae ab illo inventore veris<br>et quasi architecto beatae vitae dicta sunt explicabo. Nemo enim ipsam vuptatem<br>quia voluptas sit aspernatur aut odit aut fugit, sed quia consequuntur magni lores<br>eos qui ratione voluptatem sequi nesciunt. Neque porro quisquam est</p>
<a href="#" class="btn-orange">Read More</a>

<footer>
  <svg class="footer-shape" width="1200" height="555" viewBox="0 0 1200 555">
    <polygon points="0,140 1200,5 1200,555 0,555" fill="var(--footer)"/>
    <polygon points="0,88 190,112 0,140" fill="var(--accent-blue)"/>
    <polygon points="1030,16 1200,-2 1200,78" fill="var(--accent-blue)"/>
  </svg>

  <div class="footer-col" style="left:133px">
    <h4>CONTACT US</h4>
    <ul class="contact-list">
      <li><svg width="16" height="20" viewBox="0 0 16 20"><path d="M8 1a6.5 6.5 0 0 0-6.5 6.5C1.5 12 8 19 8 19s6.5-7 6.5-11.5A6.5 6.5 0 0 0 8 1z" fill="none" stroke="#fff" stroke-width="1.5"/><circle cx="8" cy="7.5" r="2.3" fill="none" stroke="#fff" stroke-width="1.5"/></svg>Brelvanto<br>&nbsp;Ferrow Lane, Calderby 4821<br>Westmark, Norland</li>
      <li><svg width="18" height="18" viewBox="0 0 18 18"><path d="M4 1.5l3 3.5-2 2c1 2.3 3 4.3 5.5 5.5l2-2 3.5 3-1.8 2.5C8 15 3 10 1.5 3.3z" fill="none" stroke="#fff" stroke-width="1.4" stroke-linejoin="round"/></svg>Phone :&nbsp; 1300 555 018</li>
      <li><svg width="18" height="14" viewBox="0 0 18 14"><rect x="1" y="1" width="16" height="12" fill="none" stroke="#fff" stroke-width="1.4"/><path d="M1 1l8 7 8-7" fill="none" stroke="#fff" stroke-width="1.4"/></svg>info@brelvanto-example.com</li>
    </ul>
  </div>

  <div class="footer-col" style="left:392px">
    <h4>SIGN UP TO RECEIVE EMAIL</h4>
    <p class="signup-text">Excepteur sint occaecat cupidatat non proident, sunt in culpa qui Nemo enim ipsam voluptatem</p>
    <div class="signup-form"><span class="signup-input">Enter Email</span><span class="signup-button">SUBSCRIBE</span></div>
  </div>

  <div class="footer-col" style="left:796px">
    <h4>QUICK LINKS</h4>
    <ul class="quick-links">
      <li>Home</li><li>Who We Are</li><li>Service</li><li>Investors</li><li>News</li><li>Contact</li>
    </ul>
  </div>

  <div class="footer-brand">BRELVANTO</div>
  <div class="footer-rule"></div>
  <div class="social" aria-label="Social links"><span></span><span></span><span></span><span></span></div>
  <p class="copyright">Copyright © Brelvanto 2018. All rights reserved.</p>
</footer>

</body>
</html>
```